Design NEW business card

We would like a business card using the colour deep red wine or dark navy blue textured background (patterned or not, open to suggestions) with a high gloss debossed rose gold/copper RM Roland Mercer Jewellery business name (Provided). I have included images for your review we would like to keep our currently logo and business name on the front but you can change the layout and positioning. For the back of the card we are open to all suggestions/variations.
Business
Use our current RM Roland Mercer Jewellery logo (Provided image)

```html
<!DOCTYPE html>
<html lang="en">
<head>
<meta charset="utf-8">
<title>Roland Mercer Jewellery – Business Card</title>
<link rel="stylesheet" href="https://fonts.googleapis.com/css2?family=Open+Sans:wght@400;600;700&display=swap">
<style>
  :root {
    --backdrop: #3a332f;
    --wine: #5a2229;
    --wine-deep: #4a1b21;
    --onyx: #141313;
    --onyx-soft: #1e1d1c;
    --copper: #c9957a;
    --copper-light: #dcae94;
    --paper-white: #f4eeee;
  }
  * { margin: 0; padding: 0; box-sizing: border-box; }
  html, body {
    width: 1200px; height: 844px; overflow: hidden;
    background: var(--backdrop);
    font-family: "Open Sans", Arial, sans-serif;
  }
  .stage {
    position: relative; width: 1200px; height: 844px;
    display: flex; align-items: center; justify-content: center; gap: 60px;
  }
  .card {
    position: relative; width: 525px; height: 300px; overflow: hidden;
    box-shadow: 0 14px 30px rgba(0,0,0,.45);
  }

  /* Back side: contact details */
  .card-back {
    background: radial-gradient(circle at 40% 40%, var(--wine), var(--wine-deep));
    color: var(--paper-white);
    text-align: center;
  }
  .card-back .band {
    position: absolute; left: 0; right: 0; height: 14px; background: var(--copper);
  }
  .card-back .band-top { top: 0; }
  .card-back .band-bottom { bottom: 0; }
  .holder { position: absolute; top: 62px; left: 0; right: 0; }
  .holder-name {
    font-weight: 700; font-size: 17px; letter-spacing: .3px;
    display: inline-block; padding: 0 6px 3px;
    border-bottom: 1px solid rgba(244,238,238,.7);
  }
  .holder-title { font-size: 12px; margin-top: 3px; }
  .contact { position: absolute; top: 160px; left: 0; right: 0; font-size: 13px; line-height: 17px; }
  .address { position: absolute; top: 250px; left: 0; right: 0; font-size: 14px; }

  /* Front side: brand */
  .card-front {
    background: radial-gradient(circle at 50% 45%, var(--onyx-soft), var(--onyx));
  }
  .card-front .tab {
    position: absolute; width: 26px; height: 26px; background: var(--copper);
    border-right: 3px solid #e9e6e4;
  }
  .tab-left { left: 0; bottom: 52px; }
  .tab-right { right: 0; top: 40px; border-right: none; border-left: 3px solid #e9e6e4; }
  .brand {
    position: absolute; inset: 0;
    display: flex; align-items: center; justify-content: center; gap: 14px;
  }
  .brand-mark {
    width: 14px; height: 14px; border-radius: 50%; background: var(--copper);
  }
  .brand-name {
    color: var(--copper); font-weight: 600; font-size: 22px;
    letter-spacing: 4px; text-transform: uppercase;
  }
</style>
</head>
<body>
  <main class="stage">
    <section class="card card-back" aria-label="Card back with contact details">
      <div class="band band-top"></div>
      <div class="holder">
        <div class="holder-name">DANIEL HARTLEY</div>
        <div class="holder-title">Managing Director</div>
      </div>
      <div class="contact">
        <div>044-555-0187</div>
        <div>123-555-0142</div>
        <div>hello@rolandmercer.com</div>
        <div>www.rolandmercer.com</div>
      </div>
      <div class="address">48 Harbour Lane | Northvale, AB | 204518</div>
      <div class="band band-bottom"></div>
    </section>

    <section class="card card-front" aria-label="Card front with business name">
      <div class="tab tab-right"></div>
      <div class="brand">
        <span class="brand-mark"></span>
        <span class="brand-name">Roland Mercer Jewellery</span>
      </div>
      <div class="tab tab-left"></div>
    </section>
  </main>
</body>
</html>
```